Business card for Sports Apparel business

DOUBLE SIDED DESIGN
We need business cards for a new sports apparel business. We are developing a protective headband for soccer initially.
Torvalle is focused on designing and developing head protection products to reduce the likelihood of concussion when playing sports. Exploring and understanding medical insights, material science research, current and former players experiences and governing bodies guidelines has allowed Torvalle to develop the safety, style, form and function requirements of a suitable product to bring to market.
Target Market(s)
Mums buying kits for the sons and daughters. Amateur footballers.
Industry/Entity Type
Sporting Good
Contact Information for Business Card
Martin Ashworth - CEO
Mobile: +44 7431589027
Email: martin@torvalle.co.uk
Tel: 0208 5519372
Helena Pargeter - COO
Mob: +44 7385 640117
Email: helena@torvalle.co.uk
Tel: 0208 5519372
Duncan Farrow - CCO
Mob: +44 7564 293081
Email: duncan@torvalle.co.uk
Tel: 0208 5519372
Look and feel
Each slider illustrates characteristics of the customer's brand and the style your logo design should communicate.

```html
<!DOCTYPE html>
<html lang="en">
<head>
<meta charset="utf-8">
<title>Torvalle – Business Card</title>
<link href="https://fonts.googleapis.com/css2?family=Montserrat:wght@400;600;700&display=swap" rel="stylesheet">
<style>
  :root {
    --backdrop: #1e1e1e;
    --card-grey: #666666;
    --card-white: #ffffff;
    --brand-blue: #135e98;
    --text-grey: #6e6e6e;
    --text-light: #ffffff;
  }
  * { box-sizing: border-box; margin: 0; padding: 0; }
  html, body {
    width: 1200px; height: 900px; overflow: hidden;
    background: var(--backdrop);
    font-family: "Montserrat", sans-serif;
  }
  .stage {
    width: 1200px; height: 900px;
    display: flex; flex-direction: column; align-items: center; justify-content: center;
    gap: 36px;
  }
  .card {
    position: relative;
    width: 700px; height: 400px;
    overflow: hidden;
    box-shadow: 0 10px 30px rgba(0,0,0,.5);
  }
  /* Front */
  .card-front {
    background: var(--card-grey);
    display: flex; align-items: center; justify-content: center;
  }
  .front-wordmark {
    color: var(--text-light);
    font-weight: 600;
    font-size: 64px;
    letter-spacing: 3px;
    text-transform: uppercase;
  }
  /* Back */
  .card-back { background: var(--card-white); }
  .back-wave { position: absolute; inset: 0; width: 700px; height: 400px; }
  .back-wordmark {
    position: absolute; left: 40px; top: 44px;
    color: var(--brand-blue);
    font-weight: 600; font-size: 40px; letter-spacing: 2px;
    text-transform: uppercase;
  }
  .holder {
    position: absolute; right: 40px; top: 150px; text-align: right;
  }
  .holder-name {
    color: var(--brand-blue); font-weight: 700; font-size: 20px; letter-spacing: 1.5px;
    text-transform: uppercase;
  }
  .holder-role { color: var(--text-grey); font-size: 17px; letter-spacing: 1px; margin-top: 2px; }
  .contact-list {
    position: absolute; right: 40px; bottom: 34px;
    list-style: none; color: var(--text-light); font-size: 19px; line-height: 1.45;
  }
  .contact-list li { display: flex; align-items: center; justify-content: flex-end; gap: 14px; }
  .contact-icon { width: 18px; height: 18px; flex: none; }
</style>
</head>
<body>
<main class="stage">
  <section class="card card-front" aria-label="Card front">
    <span class="front-wordmark">Torvalle</span>
  </section>

  <section class="card card-back" aria-label="Card back">
    <svg class="back-wave" viewBox="0 0 700 400" aria-hidden="true">
      <path d="M0 250 C 200 238 350 150 520 180 C 600 195 660 230 700 252 L700 400 L0 400 Z" fill="#666666"/>
      <path d="M0 220 C 150 226 280 196 380 168 C 300 196 150 232 0 238 Z" fill="#135e98"/>
      <path d="M0 250 C 200 238 350 150 520 180 C 600 195 660 230 700 252 L700 268 C 650 240 590 208 520 198 C 350 172 200 254 0 262 Z" fill="#135e98"/>
    </svg>
    <span class="back-wordmark">Torvalle</span>
    <div class="holder">
      <p class="holder-name">Martin Ashworth</p>
      <p class="holder-role">CEO</p>
    </div>
    <ul class="contact-list">
      <li>0208 551 9372
        <svg class="contact-icon" viewBox="0 0 18 18" fill="none" stroke="#fff" stroke-width="1.6"><rect x="5" y="1.5" width="8" height="15" rx="1.5"/><line x1="8" y1="14" x2="10" y2="14"/></svg>
      </li>
      <li>+44 7431589027
        <svg class="contact-icon" viewBox="0 0 18 18" fill="none" stroke="#fff" stroke-width="1.6"><path d="M4 2 L7 5 L5.5 7 C6.5 9.5 8.5 11.5 11 12.5 L13 11 L16 14 L14 16 C8 16 2 10 2 4 Z"/></svg>
      </li>
      <li>martin@torvalle.co.uk
        <svg class="contact-icon" viewBox="0 0 18 18" fill="none" stroke="#fff" stroke-width="1.6"><rect x="1.5" y="4" width="15" height="10"/><path d="M1.5 4 L9 10 L16.5 4"/></svg>
      </li>
    </ul>
  </section>
</main>
</body>
</html>
```